Oil and Gas Exploration and Production company needs a business card design

We need a business card design using our logo and colors in the logo. We want a mainstream design.

```html
<!DOCTYPE html>
<html lang="en">
<head>
<meta charset="utf-8">
<title>Kestrel Oil &amp; Gas — Business Card</title>
<link rel="stylesheet" href="https://fonts.googleapis.com/css2?family=Arimo:wght@400;700&family=Arvo:wght@700&display=swap">
<style>
  :root {
    --backdrop: #2c2c2c;
    --card: #f4f4f4;
    --ink: #111111;
    --gold: #a57c22;
    --charcoal: #3a3a3a;
    --white: #ffffff;
    --faint: rgba(0,0,0,0.07);
  }
  * { margin: 0; padding: 0; box-sizing: border-box; }
  html, body { width: 1200px; height: 997px; overflow: hidden; background: var(--backdrop); }
  .stage { position: relative; width: 1200px; height: 997px; }
  .card {
    position: absolute; left: 180px; top: 258px; width: 840px; height: 480px;
    background: linear-gradient(160deg, #ffffff 0%, var(--card) 60%, #e8e8e8 100%);
    overflow: hidden; box-shadow: 0 18px 40px rgba(0,0,0,0.55);
    font-family: "Arimo", Arial, sans-serif;
  }
  .brand { position: absolute; left: 200px; top: 70px; display: flex; align-items: center; gap: 14px; }
  .brand-dot { width: 34px; height: 34px; border-radius: 50%; background: var(--gold); }
  .brand-name { font-family: "Arvo", Georgia, serif; font-weight: 700; font-size: 50px; color: var(--ink); line-height: 1; letter-spacing: -0.5px; }
  .divider { position: absolute; left: 60px; top: 198px; width: 520px; height: 2px; background: var(--gold); }
  .person { position: absolute; left: 590px; top: 170px; }
  .person-name { font-weight: 700; font-size: 22px; color: var(--ink); letter-spacing: 0.5px; }
  .person-role { font-size: 17px; color: var(--gold); margin-top: 6px; }
  .accent-circle { position: absolute; left: 680px; top: 250px; width: 90px; height: 90px; border-radius: 50%; background: var(--faint); }
  .contacts { position: absolute; left: 60px; top: 300px; list-style: none; }
  .contacts li { display: flex; align-items: center; gap: 14px; font-size: 20px; color: var(--ink); height: 34px; }
  .contacts svg { width: 22px; height: 22px; flex: none; }
  .footer-shapes { position: absolute; left: 0; top: 0; width: 840px; height: 480px; }
  .website { position: absolute; right: 50px; top: 418px; font-weight: 700; font-size: 19px; color: var(--white); letter-spacing: 1px; }
</style>
</head>
<body>
<main class="stage">
  <section class="card" aria-label="Business card for Kestrel Oil &amp; Gas">
    <svg class="footer-shapes" viewBox="0 0 840 480" aria-hidden="true">
      <path d="M0,416 H474 C496,416 504,380 536,368 H552 C518,382 512,436 484,436 H0 Z" fill="var(--charcoal)"/>
      <path d="M0,446 H496 C524,446 530,388 566,388 H840 V480 H0 Z" fill="var(--gold)"/>
    </svg>

    <div class="brand">
      <span class="brand-dot"></span>
      <span class="brand-name">Kestrel Oil &amp; Gas</span>
    </div>

    <div class="divider"></div>
    <div class="person">
      <p class="person-name">ANDERS HALVIK</p>
      <p class="person-role">Director of Sales &amp; Marketing</p>
    </div>

    <div class="accent-circle"></div>

    <ul class="contacts">
      <li>
        <svg viewBox="0 0 22 22" aria-hidden="true"><circle cx="11" cy="11" r="11" fill="var(--gold)"/><path d="M6.5,8 C6.5,6.5 15.5,6.5 15.5,8 L14.5,9.5 L12.5,8.8 V8 H9.5 V8.8 L7.5,9.5 Z M8,11 H14 L15,15 H7 Z" fill="var(--white)"/></svg>
        555 201 3380
      </li>
      <li>
        <svg viewBox="0 0 22 22" aria-hidden="true"><circle cx="11" cy="11" r="11" fill="var(--gold)"/><rect x="8" y="5" width="6" height="12" rx="1" fill="none" stroke="var(--white)" stroke-width="1.4"/><circle cx="11" cy="15" r="0.8" fill="var(--white)"/></svg>
        555 201 7742
      </li>
      <li>
        <svg viewBox="0 0 22 22" aria-hidden="true"><circle cx="11" cy="11" r="11" fill="var(--gold)"/><rect x="6" y="7.5" width="10" height="7" fill="none" stroke="var(--white)" stroke-width="1.3"/><path d="M6,7.5 L11,11.5 L16,7.5" fill="none" stroke="var(--white)" stroke-width="1.3"/></svg>
        anders@ridgelinefuel.com
      </li>
    </ul>

    <p class="website">www.ridgelinefuel.com</p>
  </section>
</main>
</body>
</html>
```